A modern, fresh introduction to Buddhism

I need a book cover for an A6 sized book to be used both for ebook and hard copy. The author is a young, modern Buddhist teacher of high standing who has written this short intro to Buddhism in an informal Q & As format using modern, accessible language to convey profound and meaningful ideas to the general public. The author is Tibetan, but teaches worldwide and is very personable and dynamic. The cover should portray this and have a fresh yet authentic feel to it (nothing new-agey!). Please see the author's websites www.torvenmalsiteacher.org and www.vrmq.org for reference, but do not feel that the design must align completely with the website designs.

Target Market(s)

General public both in Europe and America and in Asia ranging from teenagers to the elderly. A really broad audience.

Industry/Entity Type

Teacher

Requirements
Must have
• Please include the following text that on the front cover:

A Window Onto Stillwaters

By Dorwel Tamsung Geshela

Please include the following on the back cover:

Mirun Teskavo Publications (with attached logo above it)
Nice to have
• A simplistic, artistic, and modern look without any traditional religious images.
Should not have
• No buddha images or religious images. I would prefer a more simplistic, modern and artistic look.

```html
<!DOCTYPE html>
<html lang="en">
<head>
<meta charset="utf-8">
<title>A Window Onto Stillwaters — Book Cover</title>
<link rel="stylesheet" href="https://fonts.googleapis.com/css2?family=Anton&family=Roboto+Condensed:wght@500;700&display=swap">
<style>
  :root {
    --paper: #ffffff;
    --art-pale: #fcebd6;
    --art-warm: #f3bf82;
    --art-deep: #e49a4c;
    --band-light: #f7a21c;
    --band-dark: #e27026;
    --ink-light: #ffffff;
  }
  html, body {
    margin: 0;
    padding: 0;
    width: 848px;
    height: 1200px;
    overflow: hidden;
    background: var(--paper);
  }
  .cover {
    position: relative;
    width: 848px;
    height: 1200px;
    overflow: hidden;
    background: var(--paper);
  }
  .cover-art {
    position: absolute;
    left: 0;
    top: 0;
    width: 848px;
    height: 627px;
    background: linear-gradient(165deg, var(--paper) 0%, var(--paper) 18%, var(--art-pale) 48%, var(--art-warm) 80%, var(--art-deep) 100%);
  }
  .author-band {
    position: absolute;
    left: 0;
    top: 627px;
    width: 848px;
    height: 124px;
    background: var(--band-light);
    display: flex;
    align-items: center;
    justify-content: center;
  }
  .author-name {
    margin: 0;
    font-family: "Roboto Condensed", "Arial Narrow", sans-serif;
    font-weight: 700;
    font-size: 34px;
    color: var(--ink-light);
  }
  .title-band {
    position: absolute;
    left: 0;
    top: 751px;
    width: 848px;
    height: 449px;
    background: var(--band-dark);
  }
  .book-title {
    margin: 0;
    font-family: "Anton", "Impact", sans-serif;
    font-weight: 400;
    color: var(--ink-light);
    text-transform: uppercase;
  }
  .title-line {
    position: absolute;
    left: 0;
    width: 848px;
    text-align: center;
    white-space: nowrap;
    line-height: 1.03;
  }
  .title-line-first {
    top: 74px;
    font-size: 86px;
    letter-spacing: 4px;
  }
  .title-line-second {
    top: 174px;
    font-size: 96px;
    letter-spacing: 6px;
  }
  .subtitle {
    position: absolute;
    left: 0;
    top: 324px;
    width: 848px;
    margin: 0;
    text-align: center;
    font-family: "Roboto Condensed", "Arial Narrow", sans-serif;
    font-weight: 500;
    font-size: 36px;
    color: var(--ink-light);
    text-transform: uppercase;
    white-space: nowrap;
  }
</style>
</head>
<body>
  <main class="cover">
    <div class="cover-art" role="img" aria-label="Abstract wisps of orange smoke drifting across a white background"></div>
    <header class="author-band">
      <p class="author-name">Dorwel Tamsung Geshela</p>
    </header>
    <section class="title-band">
      <h1 class="book-title">
        <span class="title-line title-line-first">A Window Onto</span>
        <span class="title-line title-line-second">Stillwaters</span>
      </h1>
      <p class="subtitle">A Short Introduction to the Buddha's Teaching</p>
    </section>
  </main>
</body>
</html>
```